Las Vegas transportation company needs a dynamic design for business cards

We are a transportation management company based in Las Vegas specializing in operating and maintaining public transit systems. We want to keep our existing logo but would like to design business cards that feature one or more transit systems (e.g. monorail, train, bus) and maybe also the Las Vegas landscape.

```html
<!DOCTYPE html>
<html lang="en">
<head>
<meta charset="utf-8">
<title>Meridian Transit Group – Business Card</title>
<link href="https://fonts.googleapis.com/css2?family=Cinzel:wght@500;600&family=Arimo:wght@400&display=swap" rel="stylesheet">
<style>
  :root {
    --page-bg: #c4c4c4;
    --card-white: #ffffff;
    --navy: #14235e;
    --sky: #8fb3e3;
    --link-blue: #4f8fe0;
    --ink: #1c1c1c;
    --back-dark: #2a2523;
    --frame-grey: #6a6a6a;
  }
  html, body {
    margin: 0;
    width: 1200px;
    height: 800px;
    overflow: hidden;
    background: var(--page-bg);
  }
  .canvas {
    width: 1200px;
    height: 800px;
    display: flex;
    align-items: center;
    justify-content: center;
    gap: 40px;
  }
  .card {
    width: 540px;
    height: 309px;
    position: relative;
    overflow: hidden;
    box-shadow: 0 6px 18px rgba(0,0,0,0.25);
  }

  /* Front */
  .card-front {
    background: var(--card-white);
    border-bottom: 2px solid var(--navy);
    box-sizing: border-box;
  }
  .divider {
    position: absolute;
    left: 268px;
    top: 24px;
    bottom: 24px;
    width: 1px;
    background: #e6e6ea;
  }
  .brand {
    position: absolute;
    left: 0;
    width: 268px;
    top: 0;
    bottom: 0;
    display: flex;
    flex-direction: column;
    align-items: center;
    justify-content: center;
  }
  .brand-row {
    display: flex;
    align-items: center;
    gap: 10px;
  }
  .brand-mark {
    width: 14px;
    height: 14px;
    border-radius: 50%;
    background: var(--sky);
  }
  .brand-name {
    font-family: "Cinzel", serif;
    font-weight: 500;
    font-size: 34px;
    letter-spacing: 1px;
    color: var(--navy);
    line-height: 1;
  }
  .brand-sub {
    margin-top: 8px;
    font-family: "Arimo", sans-serif;
    font-size: 10.5px;
    letter-spacing: 4.5px;
    color: var(--sky);
    text-transform: uppercase;
  }
  .contact {
    position: absolute;
    left: 300px;
    top: 62px;
    font-family: "Arimo", sans-serif;
    color: var(--ink);
  }
  .person-name {
    font-family: "Cinzel", serif;
    font-weight: 600;
    font-size: 19px;
    color: var(--navy);
    margin: 0;
    letter-spacing: 0.5px;
  }
  .person-title {
    font-size: 12px;
    margin: 2px 0 14px;
  }
  .contact-list {
    list-style: none;
    margin: 0 0 14px;
    padding: 0;
    font-size: 12px;
    line-height: 19px;
  }
  .contact-list li {
    display: flex;
    align-items: center;
    gap: 7px;
  }
  .contact-list svg { width: 11px; height: 11px; fill: var(--navy); flex: none; }
  .accent { color: var(--link-blue); }
  .address {
    font-size: 12px;
    line-height: 16px;
    margin: 0;
  }

  /* Back */
  .card-back {
    background: linear-gradient(180deg, #221e1d 0%, #2e2824 55%, #3a2f22 100%);
  }
  .city-night {
    position: absolute;
    inset: 0;
    background:
      radial-gradient(ellipse at 80% 30%, rgba(150,110,60,0.35), transparent 45%),
      radial-gradient(ellipse at 20% 85%, rgba(120,90,50,0.3), transparent 50%),
      linear-gradient(180deg, #241f1e 0%, #2f2823 60%, #3b3023 100%);
  }
  .photo {
    position: absolute;
    border: 2px solid var(--frame-grey);
    box-sizing: border-box;
  }
  .photo-bus {
    left: 22px; top: 70px; width: 170px; height: 150px;
    background: linear-gradient(160deg, #4d5d6b 0%, #2c3640 60%, #1d2329 100%);
  }
  .photo-loco {
    left: 150px; top: 60px; width: 195px; height: 175px;
    background: linear-gradient(135deg, #b9a35a 0%, #e4c93b 35%, #2a2e3a 65%, #8a8c92 100%);
  }
  .photo-train {
    left: 305px; top: 50px; width: 215px; height: 190px;
    background: linear-gradient(135deg, #d8dadd 0%, #c8302b 40%, #b3241f 70%, #6f7a5a 100%);
  }
</style>
</head>
<body>
<main class="canvas">

  <section class="card card-front" aria-label="Business card front">
    <div class="brand">
      <div class="brand-row">
        <span class="brand-mark"></span>
        <span class="brand-name">MERIDIAN</span>
      </div>
      <div class="brand-sub">Transit Group</div>
    </div>
    <div class="divider"></div>
    <div class="contact">
      <h1 class="person-name">DANIEL HARTLEY</h1>
      <p class="person-title">Managing Director</p>
      <ul class="contact-list">
        <li>
          <svg viewBox="0 0 24 24" aria-hidden="true"><path d="M6.6 10.8a15.1 15.1 0 0 0 6.6 6.6l2.2-2.2a1 1 0 0 1 1-.25 11.4 11.4 0 0 0 3.6.57 1 1 0 0 1 1 1V20a1 1 0 0 1-1 1A17 17 0 0 1 3 4a1 1 0 0 1 1-1h3.5a1 1 0 0 1 1 1c0 1.25.2 2.45.57 3.57a1 1 0 0 1-.25 1z"/></svg>
          044-321 654 987
        </li>
        <li>
          <svg viewBox="0 0 24 24" aria-hidden="true"><path d="M2 5h20v14H2z M2 5l10 8 10-8" stroke="#fff" stroke-width="1.5"/></svg>
          info@meridianmove.com
        </li>
        <li>
          <svg viewBox="0 0 24 24" aria-hidden="true"><circle cx="12" cy="12" r="10"/><path d="M2 12h20M12 2c3 3 3 17 0 20M12 2c-3 3-3 17 0 20" stroke="#fff" stroke-width="1.3" fill="none"/></svg>
          <span>www.<span class="accent">meridianmove</span>.com</span>
        </li>
      </ul>
      <p class="address">421, Address line goes here<br>45452,Country Name</p>
    </div>
  </section>

  <section class="card card-back" aria-label="Business card back">
    <div class="city-night" role="img" aria-label="Night view of the Las Vegas Strip with casino towers and a lit balloon sign"></div>
    <div class="photo photo-bus" role="img" aria-label="Photo of a modern city bus"></div>
    <div class="photo photo-loco" role="img" aria-label="Photo of a yellow and black diesel locomotive pulling passenger cars"></div>
    <div class="photo photo-train" role="img" aria-label="Photo of a red regional electric passenger train"></div>
  </section>

</main>
</body>
</html>
```